The Vantor Codex Book Cover

"The Vantor Codex" is a book I wrote with the slogan "Unlock Performance, Spark Engagement: Master the Art of Building Winning Cultures in Today's Hybrid World". The book is designed around a methodology that's mine and that I attached. I would love to see the graphic of the methodology integrated in the design in a very subtle way. Use colors from the model but the book cover should be catchy, modern and engaging to the eye.
Overall the book is about three key elements towards success:
- (Self) Directions (purpose)
- Human experience (people and psychological safety)
- Maximize engagement
The methodology is a FLOW so flow is something that could be incorporated as well in the concept.
Low design quality
Managers and Teams

```html
<!DOCTYPE html>
<html lang="en">
<head>
<meta charset="utf-8">
<title>The Vantor Codex — Book Cover</title>
<link href="https://fonts.googleapis.com/css2?family=Bebas+Neue&family=Montserrat:wght@400;500;600&display=swap" rel="stylesheet">
<style>
  :root{
    --backdrop:#4a4a4a;
    --paper:#ffffff;
    --brand-blue:#29a9df;
    --title-gray:#55565b;
    --ink:#111111;
    --mauve:#c36a80;
    --coral:#f07380;
    --amber:#f0bd68;
    --steel:#5b88a8;
    --sky:#5db5cc;
    --teal:#3aafa9;
    --olive:#c8c474;
  }
  *{margin:0;padding:0;box-sizing:border-box}
  html,body{width:1200px;height:1200px;overflow:hidden;background:var(--backdrop)}
  .stage{position:relative;width:1200px;height:1200px}
  .cover{
    position:absolute;left:226px;top:39px;
    width:1203px;height:1806px;
    transform:scale(0.6217);transform-origin:0 0;
    background:var(--paper);overflow:hidden;
  }
  .title-art{position:absolute;left:0;top:0;width:1203px;height:780px}
  .title-small{font-family:"Bebas Neue",sans-serif;fill:var(--title-gray)}
  .title-main{font-family:"Bebas Neue",sans-serif;fill:var(--brand-blue)}
  .title-second{font-family:"Bebas Neue",sans-serif;fill:var(--title-gray)}
  .rule{fill:var(--title-gray)}
  .flow-model{
    position:absolute;left:200px;top:790px;width:830px;height:560px;
    border-radius:280px;
    background:linear-gradient(90deg,
      var(--coral) 0%, var(--mauve) 18%, var(--amber) 36%,
      var(--steel) 52%, var(--sky) 66%, var(--teal) 82%, var(--olive) 100%);
    opacity:.85;
  }
  .tagline{
    position:absolute;left:0;width:1203px;top:1420px;text-align:center;
    font-family:Montserrat,sans-serif;color:var(--ink);
  }
  .tagline-lead{font-size:43px;font-weight:600;line-height:56px}
  .tagline-body{font-size:40px;font-weight:400;line-height:54px}
  .author-band{
    position:absolute;left:0;top:1688px;width:1203px;height:118px;
    background:var(--brand-blue);display:flex;align-items:center;justify-content:center;
  }
  .author-name{font-family:Montserrat,sans-serif;font-weight:500;font-size:62px;letter-spacing:9px;color:var(--paper)}
</style>
</head>
<body>
<div class="stage">
  <div class="cover">
    <svg class="title-art" viewBox="0 0 1203 780" xmlns="http://www.w3.org/2000/svg">
      <rect class="rule" x="96" y="128" width="410" height="8"/>
      <rect class="rule" x="703" y="128" width="410" height="8"/>
      <text class="title-small" x="605" y="180" font-size="139" text-anchor="middle">THE</text>
      <text class="title-main" x="96" y="473" font-size="390" textLength="1017" lengthAdjust="spacing">VANTOR</text>
      <text class="title-second" x="604" y="744" font-size="357" text-anchor="middle" letter-spacing="12">CODEX</text>
    </svg>

    <div class="flow-model" role="img" aria-label="Infinity-loop flow diagram of the methodology: self direction, human experience and unleashed engagement"></div>

    <div class="tagline">
      <p class="tagline-lead">Unlock Performance, Spark Engagement</p>
      <p class="tagline-body">Master the Art of Building Winning Cultures<br>in Today's Hybrid World</p>
    </div>

    <div class="author-band">
      <span class="author-name">AUTHOR NAME</span>
    </div>
  </div>
</div>
</body>
</html>
```